Verpackungen für Sekt/Champagner Flaschen
Zielgruppe
Dekoration für Hochzeiten. Tisch Dekoration für Hochzeiten. Zielgruppe alles was mit Hochzeiten zutun hat
Aufgabenstellung
Wir lassen gerade ein Tube/Dose herstellen, die als Umverpackung oder einfach Verpackung für Sekt/Champagne Flaschen dienen soll die dann auf die Tische für Hochzeit´s Deko kommt um die die Tisch Deko aufzubessern, statt einfach nur eine Sekt Flasche stehen zu haben. .Die Tube wird komplett in weiß sein und alles andere an Design soll in einem Gold sein. Mr&Mrs oder Just Married mit Herzen und alles was sonst dazu gehört, da lassen wir freie Hand.
Das Design soll Schlicht sein aber auch Luxuriös.
Durchmesser der Tube wird 8,5 cm haben und 34-35 cm sein.
Die Goldene Schrift und das Muster soll am Ende in einem Relief Lack auf der Tube erscheinen

```html
<!DOCTYPE html>
<html lang="en">
<head>
<meta charset="utf-8">
<title>Just Married – Bottle Tube Band</title>
<link rel="stylesheet" href="https://fonts.googleapis.com/css2?family=Yanone+Kaffeesatz:wght@400&display=swap">
<style>
  :root {
    --paper: #ffffff;
    --stripe-gold: #9d7b50;
    --panel-dark: #1b201b;
    --panel-frame: #a9bbcf;
    --type-gold: #b89259;
    --ornament-gold-light: #d9b66f;
    --ornament-gold-deep: #8f6a32;
  }
  html, body {
    margin: 0;
    padding: 0;
    width: 1200px;
    height: 292px;
    overflow: hidden;
    background: var(--paper);
  }
  .band {
    position: relative;
    width: 1200px;
    height: 292px;
    background: var(--paper);
  }
  .stripes {
    position: absolute;
    top: 131px;
    width: 411px;
    height: 42px;
  }
  .stripes--left { left: 0; }
  .stripes--right { left: 790px; width: 410px; }
  .stripes span {
    position: absolute;
    left: 0;
    right: 0;
    height: 10px;
    background: var(--stripe-gold);
  }
  .stripes span:nth-child(1) { top: 0; }
  .stripes span:nth-child(2) { top: 16px; }
  .stripes span:nth-child(3) { top: 32px; }

  .label {
    position: absolute;
    left: 438px;
    top: 42px;
    width: 321px;
    height: 201px;
    background: var(--panel-dark);
    border: 5px solid var(--panel-frame);
  }
  .crown {
    position: absolute;
    left: 105px;
    top: 13px;
    width: 106px;
    height: 54px;
    border-radius: 10px 10px 4px 4px;
    background: linear-gradient(180deg, var(--ornament-gold-light), var(--ornament-gold-deep));
    opacity: 0.85;
  }
  .laurel {
    position: absolute;
    top: 66px;
    width: 30px;
    height: 100px;
    border-radius: 50%;
    background: linear-gradient(180deg, var(--ornament-gold-light), var(--ornament-gold-deep));
    opacity: 0.85;
  }
  .laurel--left { left: 38px; }
  .laurel--right { left: 251px; }
  .title {
    position: absolute;
    left: 80px;
    right: 80px;
    top: 74px;
    margin: 0;
    text-align: center;
    font-family: "Yanone Kaffeesatz", "Arial Narrow", sans-serif;
    font-weight: 400;
    font-size: 40px;
    line-height: 44px;
    color: var(--type-gold);
    white-space: nowrap;
  }
</style>
</head>
<body>
  <div class="band">
    <div class="stripes stripes--left"><span></span><span></span><span></span></div>

    <div class="label">
      <div class="crown" role="img" aria-label="Gold crown ornament"></div>
      <div class="laurel laurel--left" role="img" aria-label="Gold laurel branch"></div>
      <div class="laurel laurel--right" role="img" aria-label="Gold laurel branch"></div>
      <p class="title">Just Married<br>with hearts</p>
    </div>

    <div class="stripes stripes--right"><span></span><span></span><span></span></div>
  </div>
</body>
</html>
```